Brivolt Technologies business card design

We need a business card designed with our new logo. it would be great if the card could communicate it is a technology based company.

Target Market(s)

system integrators

Industry/Entity Type

technology, IOT

Contact Information for Business Card

Name, designation, Address, telephone number, email address

Requirements
Must have
• logo and company name
Nice to have
• something to do with technology

```html
<!DOCTYPE html>
<html lang="en">
<head>
<meta charset="UTF-8">
<title>Brivolt Technologies Business Card</title>
<link href="https://fonts.googleapis.com/css2?family=Open+Sans:wght@400;600;700&display=swap" rel="stylesheet">
<style>
  :root {
    --backdrop: #353535;
    --card: #181818;
    --card-back: #141414;
    --accent: #f39a1e;
    --ink: #f2f2f2;
    --ink-soft: #d9d9d9;
  }
  * { box-sizing: border-box; margin: 0; padding: 0; }
  html, body {
    width: 1200px; height: 801px; overflow: hidden;
    background: var(--backdrop);
    font-family: "Open Sans", Arial, sans-serif;
  }
  .sheet {
    width: 1200px; height: 801px;
    display: flex; align-items: center; justify-content: center; gap: 60px;
  }
  .card {
    width: 520px; height: 298px;
    border-bottom: 3px solid var(--accent);
    border-right: 2px solid var(--accent);
    box-shadow: 0 18px 40px rgba(0,0,0,.45);
    position: relative;
  }
  .card--front {
    background: var(--card);
    display: flex; align-items: center;
  }
  .brand {
    width: 250px; padding-left: 34px;
    display: flex; align-items: center; gap: 12px;
  }
  .brand__mark { width: 34px; height: 34px; background: var(--accent); flex: none; }
  .brand__name {
    color: var(--ink); font-weight: 700; font-size: 26px; line-height: 1.05;
    letter-spacing: .5px;
  }
  .brand__name small { display: block; font-size: 11px; letter-spacing: 4.2px; margin-top: 4px; }
  .divider { width: 1.5px; height: 160px; background: var(--accent); }
  .contact { padding-left: 22px; color: var(--ink-soft); font-size: 12.5px; line-height: 1.5; }
  .contact__name { color: var(--accent); font-weight: 700; font-size: 19px; letter-spacing: .3px; line-height: 1.2; }
  .contact__role { color: var(--ink); font-size: 13px; margin-bottom: 12px; }
  .contact__address { margin-bottom: 12px; }
  .contact__row { display: flex; align-items: center; gap: 8px; }
  .contact__row svg { width: 11px; height: 11px; fill: var(--accent); flex: none; }
  .card--back {
    background: var(--card-back);
    overflow: hidden;
  }
  .card__texture {
    position: absolute; inset: 0;
    background: linear-gradient(135deg, #0e0e0e 0%, #1c1c1c 55%, #262626 100%);
  }
  .back-brand {
    position: absolute; right: 48px; top: 50%; transform: translateY(-50%);
    display: flex; align-items: center; gap: 10px;
  }
  .back-brand__mark { width: 22px; height: 22px; background: var(--accent); }
  .back-brand__name { color: var(--ink); font-weight: 700; font-size: 20px; letter-spacing: .5px; }
</style>
</head>
<body>
<main class="sheet">
  <section class="card card--front">
    <div class="brand">
      <span class="brand__mark"></span>
      <div class="brand__name">BRIVOLT<small>TECHNOLOGIES</small></div>
    </div>
    <div class="divider"></div>
    <div class="contact">
      <div class="contact__name">DANIEL REYES</div>
      <div class="contact__role">President</div>
      <div class="contact__address">1180 Harbor Crest Dr<br>Lakemont CA 90000</div>
      <div class="contact__row">
        <svg viewBox="0 0 24 24"><path d="M6.6 10.8a15 15 0 0 0 6.6 6.6l2.2-2.2c.3-.3.7-.4 1-.2 1.1.4 2.3.6 3.6.6.6 0 1 .4 1 1V20c0 .6-.4 1-1 1A17 17 0 0 1 3 4c0-.6.4-1 1-1h3.5c.6 0 1 .4 1 1 0 1.3.2 2.5.6 3.6.1.3 0 .7-.2 1z"/></svg>
        555-201-4418
      </div>
      <div class="contact__row">
        <svg viewBox="0 0 24 24"><path d="M2 5h20v14H2z M2 5l10 8 10-8" /></svg>
        info@brivolttech.com
      </div>
      <div class="contact__row">
        <svg viewBox="0 0 24 24"><circle cx="12" cy="12" r="10"/></svg>
        www.brivolttech.com
      </div>
    </div>
  </section>

  <section class="card card--back">
    <div class="card__texture" role="img" aria-label="Tonal repeating pattern of the company symbol in gloss black"></div>
    <div class="back-brand">
      <span class="back-brand__mark"></span>
      <span class="back-brand__name">BRIVOLT</span>
    </div>
  </section>
</main>
</body>
</html>
```